Menu Design Project

We trying to replace old flyer/menu with some new design.
hello this is my old menu i attached in email and my logo, the text you can pick from the menu and and i also attached some new picture for the food ,with my menu size unfold. front and back and then fold to 3.5" * 11". please show me what best can you do .Trifold is fine but must have image of food,
this is indian Restaurant
thats fine to have trifold menu design do to short time

Need to add also food picture on menu

Font styles to use
Serif
Decorative
Script

Colors

Designer to choose colors to be used in the design.

Requirements
Must have
• food image on menu
• trifold is fine ( do to short time)
• menu has to elegant ,color or text can be optional, Menu need to be neat and clean no too much rush on between the words .

```html
<!DOCTYPE html>
<html lang="en">
<head>
<meta charset="utf-8">
<title>Crown Spice Palace – Trifold Menu</title>
<link href="https://fonts.googleapis.com/css2?family=Crimson+Pro:ital,wght@0,400;0,700;1,400&family=Cormorant+Garamond:wght@500;600;700&family=Great+Vibes&display=swap" rel="stylesheet">
<style>
:root{
  --bg:#e6e6e4;
  --board:#222222;
  --board-edge:#161616;
  --gold:#f3c415;
  --gold-deep:#b8901a;
  --paper:#ffffff;
  --muted:#b9a878;
  --rule:rgba(255,255,255,.85);
}
*{box-sizing:border-box;margin:0;padding:0}
html,body{width:1200px;height:1200px;overflow:hidden;background:var(--bg)}
body{position:relative;font-family:'Crimson Pro',serif;color:var(--paper)}
.sheet{position:absolute;left:40px;width:1120px;height:530px;padding:10px;display:grid;grid-template-columns:repeat(3,1fr);gap:10px;
  background:radial-gradient(ellipse at 50% 40%,#2e2e2e 0%,var(--board) 55%,var(--board-edge) 100%);box-shadow:0 4px 14px rgba(0,0,0,.35)}
.sheet--outside{top:30px}
.sheet--inside{top:610px}
.panel{border:1px dashed var(--rule);padding:8px 12px;overflow:hidden;display:flex;flex-direction:column}
.heading{display:flex;align-items:center;justify-content:center;gap:6px;margin:5px 0 7px}
.heading:first-child{margin-top:2px}
.plate{background:var(--gold);color:#141414;font:18px/1 'Great Vibes',cursive;padding:3px 14px 2px;border:1px solid #141414;outline:1px solid var(--gold);box-shadow:0 0 0 2px var(--gold)}
.flourish{width:30px;height:16px;border-radius:50%;background:linear-gradient(90deg,var(--gold-deep),var(--gold));opacity:.8}
.cols{display:grid;grid-template-columns:1fr 1fr;column-gap:16px}
.col{display:flex;flex-direction:column;gap:3px}
.item{display:grid;grid-template-columns:1fr auto;column-gap:4px;align-items:baseline}
.name{font:700 7.6px/1.15 'Crimson Pro',serif;text-transform:uppercase;letter-spacing:.1px}
.price{font:700 7.6px/1.15 'Crimson Pro',serif}
.desc{grid-column:1/-1;font:italic 5.8px/1.15 'Crimson Pro',serif;color:var(--muted)}
.note{text-align:center;font:700 7.6px 'Crimson Pro',serif;margin:10px 0 6px}
.divider{display:block;width:70px;height:14px;margin:0 auto 6px;border-radius:50%;background:linear-gradient(90deg,var(--gold-deep),var(--gold));opacity:.8}
.contact{text-align:center;font:700 9.5px/1.35 'Crimson Pro',serif}
.dish{display:block;margin:8px auto 0;border-radius:50%;border:3px solid #f2f2f2;box-shadow:0 2px 6px rgba(0,0,0,.5)}
.dish--grill{width:150px;height:56px;background:radial-gradient(ellipse,#c0471c 0%,#8d2e10 45%,#f1f1f1 60%)}
.dish--noodle{width:72px;height:72px;background:radial-gradient(circle,#d9b46a 0%,#c7954a 40%,#f4f4f4 55%)}
.dish--seafood{width:110px;height:44px;border-radius:6px;background:radial-gradient(ellipse,#c4561f 0%,#a33d15 45%,#f2f2f2 62%)}
.dish--curry{width:64px;height:64px;background:radial-gradient(circle,#e2c8a0 0%,#b98a52 40%,#2a2a2a 55%,#f2f2f2 68%)}
.dish--biryani{width:130px;height:52px;background:radial-gradient(ellipse,#d9a441 0%,#b87a25 45%,#f3f3f3 62%)}
.spacer{flex:1}
/* cover panel */
.cover{align-items:center;text-align:center}
.crest{width:62px;height:62px;border:2px solid var(--paper);border-radius:50%;margin-top:6px}
.brand{font:600 27px/1.1 'Cormorant Garamond',serif;margin-top:10px}
.brand-rule{width:85%;height:1px;background:var(--paper);margin:5px 0}
.tagline{font:700 14px/1.1 'Cormorant Garamond',serif;letter-spacing:.6px}
.frame{position:relative;width:290px;height:250px;margin-top:16px;display:flex;align-items:center;justify-content:center}
.frame-ornament{position:absolute;inset:0;border-radius:14px;background:radial-gradient(ellipse,transparent 52%,rgba(243,196,21,.55) 53%,rgba(184,144,26,.35) 75%,transparent 76%)}
.photo{position:relative;width:180px;height:170px;border:3px solid var(--gold);outline:2px solid #141414;box-shadow:0 0 0 4px var(--gold);
  background:linear-gradient(180deg,#8a6a3e 0%,#c8a46a 35%,#6d4a2c 65%,#d8c6a4 100%)}
.served{font:500 17px/1 'Cormorant Garamond',serif;margin-top:22px}
.halal{display:flex;align-items:center;gap:8px;margin-top:6px;font:700 22px/1 'Cormorant Garamond',serif;letter-spacing:.5px}
.halal::before,.halal::after{content:"";width:56px;height:1px;background:var(--paper)}
.web{margin-top:10px;color:var(--gold);font:italic 700 10px 'Crimson Pro',serif;letter-spacing:2.4px}
</style>
</head>
<body>

<section class="sheet sheet--outside">
  <!-- Vegetarian handi, breads, desserts -->
  <div class="panel">
    <div class="heading"><span class="flourish" role="img" aria-label="gold scroll ornament"></span><span class="plate">Handi (Vegetarian)</span><span class="flourish" role="img" aria-label="gold scroll ornament"></span></div>
    <div class="cols">
      <div class="col">
        <div class="item"><span class="name">Paneer Makhni</span><span class="price">$8.99</span><span class="desc">cheese in creamy tomato sauce</span></div>
        <div class="item"><span class="name">Paneer Tikka Masala</span><span class="price">$8.99</span><span class="desc">grilled cheese, peppers, onion gravy</span></div>
        <div class="item"><span class="name">Kadai Paneer</span><span class="price">$8.99</span><span class="desc">cheese cubes tossed in a kadai</span></div>
        <div class="item"><span class="name">Palak Paneer</span><span class="price">$8.44</span><span class="desc">fresh spinach with cheese cubes</span></div>
        <div class="item"><span class="name">Mutter Paneer</span><span class="price">$8.49</span><span class="desc">green peas and cheese curry</span></div>
        <div class="item"><span class="name">Shahi Paneer</span><span class="price">$8.99</span><span class="desc">cheese in rich creamy sauce</span></div>
        <div class="item"><span class="name">Paneer Bhurji</span><span class="price">$10.99</span><span class="desc">grated cheese with green pepper</span></div>
        <div class="item"><span class="name">Malai Kofta</span><span class="price">$8.99</span><span class="desc">veggie balls in almond sauce</span></div>
        <div class="item"><span class="name">Navratan Korma</span><span class="price">$8.99</span><span class="desc">mixed vegetables in cashew sauce</span></div>
        <div class="item"><span class="name">Kaju Mushroom Mutter</span><span class="price">$9.29</span><span class="desc">mushroom, cashew, peas in cream</span></div>
        <div class="item"><span class="name">Methi Malai Mutter</span><span class="price">$9.29</span><span class="desc">fenugreek and peas, lightly creamed</span></div>
        <div class="item"><span class="name">Aloo Gobhi</span><span class="price">$8.50</span><span class="desc">dry potato and cauliflower</span></div>
      </div>
      <div class="col">
        <div class="item"><span class="name">Bhindi Masala</span><span class="price">$8.50</span><span class="desc">okra sauteed with onion</span></div>
        <div class="item"><span class="name">Achari Baigan</span><span class="price">$8.49</span><span class="desc">baby eggplant in pickle spice</span></div>
        <div class="item"><span class="name">Baigan Bharta</span><span class="price">$8.49</span><span class="desc">roasted mashed eggplant</span></div>
        <div class="item"><span class="name">Vegetable Jalfrezi</span><span class="price">$8.49</span><span class="desc">mixed vegetables, mildly spiced</span></div>
        <div class="item"><span class="name">Zeera Aloo</span><span class="price">$7.50</span><span class="desc">potatoes with cumin seeds</span></div>
        <div class="item"><span class="name">Sarson Ka Saag</span><span class="price">$8.49</span><span class="desc">mustard greens, Punjabi style</span></div>
        <div class="item"><span class="name">Chana Peshawari</span><span class="price">$8.49</span><span class="desc">chickpeas in exotic spices</span></div>
        <div class="item"><span class="name">Chana Palak</span><span class="price">$8.49</span><span class="desc">chickpeas with fresh spinach</span></div>
        <div class="item"><span class="name">Punjabi Kadi</span><span class="price">$8.49</span><span class="desc">yogurt curry with fritters</span></div>
        <div class="item"><span class="name">Daal Tarka Yellow</span><span class="price">$8.49</span><span class="desc">yellow lentils, garlic tempering</span></div>
        <div class="item"><span class="name">Daal Tarka Black</span><span class="price">$8.49</span><span class="desc">black lentils with tomato</span></div>
        <div class="item"><span class="name">Daal Makhni</span><span class="price">$8.49</span><span class="desc">slow-simmered lentils in butter</span></div>
      </div>
    </div>
    <div class="heading"><span class="flourish" role="img" aria-label="gold scroll ornament"></span><span class="plate">Tandoori Bread</span><span class="flourish" role="img" aria-label="gold scroll ornament"></span></div>
    <div class="cols">
      <div class="col">
        <div class="item"><span class="name">Tandoori Roti</span><span class="price">$1.75</span><span class="desc">whole wheat, clay oven</span></div>
        <div class="item"><span class="name">Tandoori Naan</span><span class="price">$1.75</span><span class="desc">soft white bread</span></div>
        <div class="item"><span class="name">Garlic Naan</span><span class="price">$2.50</span><span class="desc">naan with fresh garlic</span></div>
        <div class="item"><span class="name">Lachha Paratha</span><span class="price">$2.50</span><span class="desc">layered whole wheat bread</span></div>
        <div class="item"><span class="name">Onion Kulcha</span><span class="price">$2.99</span><span class="desc">stuffed with chopped onion</span></div>
      </div>
      <div class="col">
        <div class="item"><span class="name">Aloo Paratha</span><span class="price">$2.99</span><span class="desc">stuffed with spiced potato</span></div>
        <div class="item"><span class="name">Gobhi Paratha</span><span class="price">$3.50</span><span class="desc">stuffed with cauliflower</span></div>
        <div class="item"><span class="name">Pudina Paratha</span><span class="price">$2.99</span><span class="desc">layered bread with mint</span></div>
        <div class="item"><span class="name">Keema Naan</span><span class="price">$3.99</span><span class="desc">stuffed with minced chicken</span></div>
        <div class="item"><span class="name">Jalebi Paratha</span><span class="price">$2.99</span><span class="desc">rich, spiral layered bread</span></div>
      </div>
    </div>
    <div class="heading"><span class="flourish" role="img" aria-label="gold scroll ornament"></span><span class="plate">Desserts</span><span class="flourish" role="img" aria-label="gold scroll ornament"></span></div>
    <div class="cols">
      <div class="col"><div class="item"><span class="name">Kheer</span><span class="price">$3.99</span><span class="desc">rice pudding with cardamom, nuts</span></div></div>
      <div class="col"><div class="item"><span class="name">Rasmalai (3pcs)</span><span class="price">$3.99</span><span class="desc">cheese dumplings in saffron milk</span></div></div>
    </div>
  </div>

  <!-- Desserts cont., beverages, cocktails, contact -->
  <div class="panel">
    <div class="cols">
      <div class="col">
        <div class="item"><span class="name">Gulab Jamun (3 pc.)</span><span class="price">$3.99</span><span class="desc">milk dumplings in warm syrup</span></div>
        <div class="item"><span class="name">Gajar Halwa</span><span class="price">$3.99</span><span class="desc">carrot cooked with milk, nuts</span></div>
      </div>
      <div class="col">
        <div class="item"><span class="name">Ice Cream</span><span class="price">$3.50</span><span class="desc">mango, vanilla or chocolate</span></div>
      </div>
    </div>
    <div class="heading"><span class="flourish" role="img" aria-label="gold scroll ornament"></span><span class="plate">Beverages</span><span class="flourish" role="img" aria-label="gold scroll ornament"></span></div>
    <div class="cols">
      <div class="col">
        <div class="item"><span class="name">Mango Lassi</span><span class="price">$3.50</span><span class="desc">refreshing yogurt mango drink</span></div>
        <div class="item"><span class="name">Lassi (Sweet or Salted)</span><span class="price">$3.50</span><span class="desc">a delicious yogurt drink</span></div>
        <div class="item"><span class="name">Fresh Lemonade</span><span class="price">$2.99</span><span class="desc">sweet or sour, freshly made</span></div>
        <div class="item"><span class="name">Pina Colada Virgin</span><span class="price">$3.99</span><span class="desc">pineapple and coconut</span></div>
        <div class="item"><span class="name">Strawberry Daiquiri Virgin</span><span class="price">$3.99</span><span class="desc">strawberry and citrus blend</span></div>
        <div class="item"><span class="name">Orange Juice</span><span class="price">$2.99</span></div>
        <div class="item"><span class="name">Pineapple Juice</span><span class="price">$2.99</span></div>
      </div>
      <div class="col">
        <div class="item"><span class="name">Mango Juice</span><span class="price">$2.99</span></div>
        <div class="item"><span class="name">Masala Tea</span><span class="price">$1.99</span><span class="desc">Indian tea with aromatic spices</span></div>
        <div class="item"><span class="name">Coffee</span><span class="price">$1.99</span></div>
        <div class="item"><span class="name">Cold Beers</span><span class="price"></span><span class="desc">lager, light, pale ale and more</span></div>
        <div class="item"><span class="name">Indian Beers</span><span class="price"></span></div>
        <div class="item"><span class="name">Wines (750ml/1.5 Ltr)</span><span class="price">$22.00/$38.00</span><span class="desc">red, white, rosé, sparkling</span></div>
        <div class="item"><span class="name" style="text-transform:none">Cola, Lemon Soda, Ginger Ale</span><span class="price">$1.50</span></div>
      </div>
    </div>
    <div class="heading"><span class="flourish" role="img" aria-label="gold scroll ornament"></span><span class="plate">Cocktails</span><span class="flourish" role="img" aria-label="gold scroll ornament"></span></div>
    <div class="cols">
      <div class="col">
        <div class="item"><span class="name">Martini Coctail</span><span class="price">$6.99</span><span class="desc">shaken, served chilled</span></div>
        <div class="item"><span class="name">Mojito Coctail</span><span class="price">$8.99</span><span class="desc">mint, lime and soda</span></div>
        <div class="item"><span class="name">Island Rum Coctail</span><span class="price">$5.99</span><span class="desc">light rum, citrus twist</span></div>
        <div class="item"><span class="name">Mai Tai Coctail</span><span class="price">$4.99</span><span class="desc">rum, orange, almond</span></div>
        <div class="item"><span class="name">Bloody Mary</span><span class="price">$9.99</span><span class="desc">tomato, spice, celery</span></div>
        <div class="item"><span class="name">Dalquiri Coctail</span><span class="price">$10.99</span><span class="desc">rum, lime, sugar</span></div>
        <div class="item"><span class="name">Tropical Storm</span><span class="price">$6.99</span><span class="desc">fruit punch with rum</span></div>
        <div class="item"><span class="name">Pina Colada</span><span class="price">$6.99</span><span class="desc">pineapple, coconut, rum</span></div>
        <div class="item"><span class="name">Tequila Blond</span><span class="price">$6.99</span><span class="desc">tequila with citrus</span></div>
      </div>
      <div class="col">
        <div class="item"><span class="name">Banana D Coctail</span><span class="price">$6.99</span><span class="desc">banana blended frozen</span></div>
        <div class="item"><span class="name">Cuban Rhum</span><span class="price">$8.99</span><span class="desc">dark rum on ice</span></div>
        <div class="item"><span class="name">Mango Dalquiri</span><span class="price">$5.99</span><span class="desc">fresh mango, rum</span></div>
        <div class="item"><span class="name">Cuban Mojito</span><span class="price">$4.99</span><span class="desc">classic mint and lime</span></div>
        <div class="item"><span class="name">Bloody Mary</span><span class="price">$9.99</span><span class="desc">house spiced mix</span></div>
        <div class="item"><span class="name">Dalquiri Coctail</span><span class="price">$10.99</span><span class="desc">strawberry or classic</span></div>
        <div class="item"><span class="name">Mai Tai Cocktail</span><span class="price">$6.99</span><span class="desc">tropical rum blend</span></div>
        <div class="item"><span class="name">Bloody Ma Cocktail</span><span class="price">$6.99</span><span class="desc">tomato, lemon, pepper</span></div>
        <div class="item"><span class="name">Datquiri Cocktail</span><span class="price">$5.99</span><span class="desc">lime and cane sugar</span></div>
      </div>
    </div>
    <p class="note">[ Prices subject to change without Notice Tax is not included in these prices ]</p>
    <span class="divider" role="img" aria-label="gold scroll ornament"></span>
    <div class="contact">
      <p>204-15 Meridian Ave., Fairview, NY 11500</p>
      <p>Email: HELLO@CROWNSPICEPALACE.EXAMPLE</p>
      <p>Tel: 555-210-4400, 555-210-4401</p>
      <p>Fax: 555-210-4402</p>
    </div>
  </div>

  <!-- Cover -->
  <div class="panel cover">
    <span class="crest"></span>
    <h1 class="brand">Crown Spice Palace</h1>
    <span class="brand-rule"></span>
    <p class="tagline">RESTAURANT &amp; BANQUET HALL</p>
    <div class="frame">
      <span class="frame-ornament" role="img" aria-label="gold scroll ornament framing the photo"></span>
      <div class="photo" role="img" aria-label="photo of the restaurant dining hall interior"></div>
    </div>
    <p class="served">WE SERVED</p>
    <p class="halal">HALAL FOOD</p>
    <p class="web">www.crownspicepalace.example</p>
  </div>
</section>

<section class="sheet sheet--inside">
  <!-- Appetizers -->
  <div class="panel">
    <div class="heading"><span class="flourish" role="img" aria-label="gold scroll ornament"></span><span class="plate">Vegetarian Appetizer</span><span class="flourish" role="img" aria-label="gold scroll ornament"></span></div>
    <div class="cols">
      <div class="col">
        <div class="item"><span class="name">Vegetable Samosa (2 pc.)</span><span class="price">$2.99</span><span class="desc">spiced potatoes and peas in pastry</span></div>
        <div class="item"><span class="name">Samosa Chaat (2 pc.)</span><span class="price">$7.49</span><span class="desc">samosa with chutney and chickpeas</span></div>
        <div class="item"><span class="name">Aloo Tikki Chaat (4 pc.)</span><span class="price">$6.99</span><span class="desc">potato patties with chutney</span></div>
        <div class="item"><span class="name">Mix Veg. Pakora</span><span class="price">$6.50</span><span class="desc">vegetable fritters in chickpea batter</span></div>
        <div class="item"><span class="name">Papri Chaat</span><span class="price">$6.50</span><span class="desc">crisp wafers, potato, tamarind</span></div>
        <div class="item"><span class="name">Dahi Bhalla</span><span class="price">$6.99</span><span class="desc">lentil dumplings, yogurt, mint</span></div>
      </div>
      <div class="col">
        <div class="item"><span class="name">Paneer Pakora (7 pc.)</span><span class="price">$8.95</span><span class="desc">cheese fritters dipped in batter</span></div>
        <div class="item"><span class="name">Vegetable Seem Kabab</span><span class="price">$8.99</span><span class="desc">minced vegetables on skewers</span></div>
        <div class="item"><span class="name">Paneer Tikka Tandoori</span><span class="price">$11.99</span><span class="desc">grilled cheese, pepper, onion</span></div>
        <div class="item"><span class="name">Chhole Bhature (2 pc.)</span><span class="price">$8.99</span><span class="desc">puffy bread with chickpea curry</span></div>
        <div class="item"><span class="name">Stuffed Paneer Pakora (6 pc.)</span><span class="price">$8.50</span><span class="desc">cheese stuffed with spices</span></div>
        <div class="item"><span class="name">Chatpati Aloo Chaat</span><span class="price">$7.50</span></div>
      </div>
    </div>
    <div class="heading"><span class="flourish" role="img" aria-label="gold scroll ornament"></span><span class="plate">Non Vegetarian Appetizer</span><span class="flourish" role="img" aria-label="gold scroll ornament"></span></div>
    <div class="cols">
      <div class="col">
        <div class="item"><span class="name">Chicken Samosa (2 pc.)</span><span class="price">$5.99</span><span class="desc">spicy minced chicken in pastry</span></div>
        <div class="item"><span class="name">Chicken Pakora</span><span class="price">$10.99</span><span class="desc">lightly spiced chicken fritters</span></div>
        <div class="item"><span class="name">Fish Amritsari</span><span class="price">$14.59</span><span class="desc">mildly spiced battered fish</span></div>
        <div class="item"><span class="name">Tawa Chicken</span><span class="price">$12.99</span><span class="desc">chicken on griddle with pepper</span></div>
        <div class="item"><span class="name">Garlic Shrimp</span><span class="price">$12.99</span><span class="desc">shrimp in garlic chef sauce</span></div>
        <div class="item"><span class="name">Spicy Wings (8 pc.)</span><span class="price">$8.99</span><span class="desc">hot and spicy buffalo wings</span></div>
        <div class="item"><span class="name">Tandoori Chicken</span><span class="price">$8.99/12.99</span><span class="desc">marinated in yogurt, clay oven</span></div>
        <div class="item"><span class="name">Chicken Seekh Kabab</span><span class="price">$10.49</span><span class="desc">minced chicken with fresh herbs</span></div>
        <div class="item"><span class="name">Lamb Seekh Kabab</span><span class="price">$12.29</span><span class="desc">ground lamb with herbs, spices</span></div>
        <div class="item"><span class="name">Chicken Tikka</span><span class="price">$11.49</span><span class="desc">boneless chicken, yogurt marinade</span></div>
      </div>
      <div class="col">
        <div class="item"><span class="name">Chicken Malai Kabab</span><span class="price">$11.99</span><span class="desc">chicken in cream and cheese</span></div>
        <div class="item"><span class="name">Achari Tikka</span><span class="price">$11.99</span><span class="desc">chicken in pickle spices</span></div>
        <div class="item"><span class="name">Afghani Chicken</span><span class="price">$12.99</span><span class="desc">mildly spiced, cashew cream</span></div>
        <div class="item"><span class="name">Fish Tikka Tandoori</span><span class="price">$14.99</span><span class="desc">fish marinated with ginger</span></div>
        <div class="item"><span class="name">Salmon Fish</span><span class="price">$15.29</span><span class="desc">salmon with herbs and spices</span></div>
        <div class="item"><span class="name">Tawa Fish</span><span class="price">$14.99</span><span class="desc">fish on griddle, fresh herbs</span></div>
        <div class="item"><span class="name">Tandoori Shrimp (6 pc.)</span><span class="price">$14.99</span><span class="desc">jumbo shrimp with spices</span></div>
        <div class="item"><span class="name">Lamb Chop (5 pc.)</span><span class="price">$22.99</span><span class="desc">rack of lamb with herbs</span></div>
        <div class="item"><span class="name">Tandoori Mix Grill</span><span class="price">$18.49</span><span class="desc">chicken, seekh kabab and shrimp</span></div>
      </div>
    </div>
    <div class="spacer"></div>
    <span class="dish dish--grill" role="img" aria-label="photo of a plate of grilled tandoori chicken"></span>
  </div>

  <!-- Indo-Chinese, soups, seafood -->
  <div class="panel">
    <div class="heading"><span class="flourish" role="img" aria-label="gold scroll ornament"></span><span class="plate">Indo-Chinese</span><span class="flourish" role="img" aria-label="gold scroll ornament"></span></div>
    <div class="cols">
      <div class="col">
        <div class="item"><span class="name">Chilli Paneer</span><span class="price">$10.99</span><span class="desc">cheese with peppers, onion</span></div>
        <div class="item"><span class="name">Chilli Mushroom</span><span class="price">$9.99</span><span class="desc">mushroom in spicy sauce</span></div>
        <div class="item"><span class="name">Chilli Gobhi</span><span class="price">$9.99</span><span class="desc">crisp cauliflower, chilli sauce</span></div>
        <div class="item"><span class="name">Vegetable Manchurian</span><span class="price">$10.50</span><span class="desc">vegetable balls in special sauce</span></div>
        <div class="item"><span class="name">Vegetable Chowmein</span><span class="price">$8.30</span><span class="desc">stir-fry noodles with vegetables</span></div>
        <div class="item"><span class="name">Vegetable Spring Roll</span><span class="price">$6.99</span><span class="desc">carrot and cabbage wrapped crisp</span></div>
        <div class="item"><span class="name">Chilli Chicken</span><span class="price">$10.99</span><span class="desc">boneless chicken, bell pepper</span></div>
      </div>
      <div class="col">
        <div class="item"><span class="name">Chilli Fish</span><span class="price">$13.99</span><span class="desc">fish with peppers and onion</span></div>
        <div class="item"><span class="name">Chilli Shrimp</span><span class="price">$12.99</span><span class="desc">shrimp in spicy chilli sauce</span></div>
        <div class="item"><span class="name">Chicken Manchurian</span><span class="price">$10.99</span><span class="desc">chicken balls in garlic sauce</span></div>
        <div class="item"><span class="name">Chicken Chowmein</span><span class="price">$9.99</span><span class="desc">noodles with chicken, vegetables</span></div>
        <span class="dish dish--noodle" role="img" aria-label="photo of a bowl of noodles with chopsticks"></span>
      </div>
    </div>
    <div class="heading"><span class="flourish" role="img" aria-label="gold scroll ornament"></span><span class="plate">Soup, Salad &amp; Raita</span><span class="flourish" role="img" aria-label="gold scroll ornament"></span></div>
    <div class="cols">
      <div class="col">
        <div class="item"><span class="name">Tomato Soup</span><span class="price">$3.99</span><span class="desc">a simple fresh tomato soup</span></div>
        <div class="item"><span class="name">Vegetarian Soup</span><span class="price">$3.99</span><span class="desc">soup with variety of vegetables</span></div>
        <div class="item"><span class="name">Chicken Soup</span><span class="price">$4.50</span><span class="desc">chicken broth with herbs</span></div>
        <div class="item"><span class="name">Hot N Sour Soup (chicken or veg)</span><span class="price">$4.99</span><span class="desc">tangy and spicy broth</span></div>
      </div>
      <div class="col">
        <div class="item"><span class="name">Fresh Garden Salad</span><span class="price">$4.50</span></div>
        <div class="item"><span class="name">Masala Salad</span><span class="price">$5.99</span><span class="desc">spiced fresh salad</span></div>
        <div class="item"><span class="name">Mix Raita</span><span class="price">$3.99</span></div>
        <div class="item"><span class="name">Boondi Raita</span><span class="price">$3.99</span></div>
        <div class="item"><span class="name">Pudina Raita</span><span class="price">$3.99</span></div>
        <div class="item"><span class="name">Plain Dahi</span><span class="price">$3.50</span></div>
      </div>
    </div>
    <div class="heading"><span class="flourish" role="img" aria-label="gold scroll ornament"></span><span class="plate">Seafood Special</span><span class="flourish" role="img" aria-label="gold scroll ornament"></span></div>
    <div class="cols">
      <div class="col">
        <div class="item"><span class="name">Kadai Fish</span><span class="price">$13.99</span><span class="desc">fish with bell pepper, onion</span></div>
        <div class="item"><span class="name">Fish Curry</span><span class="price">$13.99</span><span class="desc">fish in traditional curry</span></div>
        <div class="item"><span class="name">Fish Masala</span><span class="price">$13.99</span><span class="desc">spiced tomato onion gravy</span></div>
        <div class="item"><span class="name">Goa Fish Curry</span><span class="price">$12.59</span><span class="desc">coconut, tangy and spicy</span></div>
        <div class="item"><span class="name">Fish Tikka Masala</span><span class="price">$12.59</span><span class="desc">grilled fish in creamy sauce</span></div>
        <div class="item"><span class="name">Shrimp Curry</span><span class="price">$12.99</span><span class="desc">shrimp in onion gravy</span></div>
        <div class="item"><span class="name">Shrimp Bhuna</span><span class="price">$12.99</span><span class="desc">shrimp with shredded onions</span></div>
      </div>
      <div class="col">
        <div class="item"><span class="name">Shrimp Vindaloo</span><span class="price">$12.99</span><span class="desc">shrimp, potato, hot chilli</span></div>
        <div class="item"><span class="name">Kadai Shrimp</span><span class="price">$12.99</span><span class="desc">with ginger, onion, tomato</span></div>
        <div class="item"><span class="name">Shrimp Masala</span><span class="price">$12.99</span><span class="desc">shrimp in spiced sauce</span></div>
        <div class="item"><span class="name">Shrimp Saag</span><span class="price">$12.99</span><span class="desc">shrimp with fresh spinach</span></div>
        <span class="dish dish--seafood" role="img" aria-label="photo of a plated seafood curry"></span>
      </div>
    </div>
  </div>

  <!-- Non-veg handi, biryani -->
  <div class="panel">
    <div class="heading"><span class="flourish" role="img" aria-label="gold scroll ornament"></span><span class="plate">Handi Special (Non-Veg)</span><span class="flourish" role="img" aria-label="gold scroll ornament"></span></div>
    <div class="cols">
      <div class="col">
        <div class="item"><span class="name">Chicken Makhni</span><span class="price">$9.49</span><span class="desc">chicken in clay oven, then butter sauce</span></div>
        <div class="item"><span class="name">Chicken Tikka Masala</span><span class="price">$9.49</span><span class="desc">roasted chicken with bell pepper</span></div>
        <div class="item"><span class="name">Chicken Curry</span><span class="price">$9.29</span><span class="desc">chicken with ginger and onion</span></div>
        <div class="item"><span class="name">Chicken Korma</span><span class="price">$9.29</span><span class="desc">chicken in nut cashew sauce</span></div>
        <div class="item"><span class="name">Kadai Chicken</span><span class="price">$9.29</span><span class="desc">boneless chicken with pepper</span></div>
        <div class="item"><span class="name">Chicken Saag</span><span class="price">$8.99</span><span class="desc">chicken with fresh spinach</span></div>
        <div class="item"><span class="name">Chicken Jalfrezi</span><span class="price">$8.99</span><span class="desc">chicken with fresh vegetables</span></div>
        <div class="item"><span class="name">Chicken Masala</span><span class="price">$9.99</span><span class="desc">chicken in chef's rich sauce</span></div>
        <div class="item"><span class="name">Chicken Vindaloo</span><span class="price">$9.99</span><span class="desc">chicken and potato, hot spices</span></div>
        <div class="item"><span class="name">Goat Curry</span><span class="price">$10.29</span><span class="desc">traditional goat on the bone</span></div>
        <div class="item"><span class="name">Goat Masala</span><span class="price">$11.29</span><span class="desc">goat in a thick spiced sauce</span></div>
        <div class="item"><span class="name">Kadai Goat</span><span class="price">$10.29</span><span class="desc">goat with pepper and onion</span></div>
      </div>
      <div class="col">
        <div class="item"><span class="name">Goat Saag</span><span class="price">$9.99</span><span class="desc">goat with fresh spinach</span></div>
        <div class="item"><span class="name">Goat Vindaloo</span><span class="price">$9.99</span><span class="desc">goat, vinegar and hot chilli</span></div>
        <div class="item"><span class="name">Chicken Keema Mutter</span><span class="price">$10.99</span><span class="desc">minced chicken with green peas</span></div>
        <div class="item"><span class="name">Lamb Curry</span><span class="price">$10.99</span><span class="desc">lamb in onion tomato gravy</span></div>
        <div class="item"><span class="name">Lamb Rogan Josh</span><span class="price">$10.99</span><span class="desc">lamb cooked in Kashmiri style</span></div>
        <div class="item"><span class="name">Lamb Saag</span><span class="price">$10.99</span><span class="desc">lamb with fresh spinach</span></div>
        <div class="item"><span class="name">Lamb Korma</span><span class="price">$10.99</span><span class="desc">lamb in almond cashew sauce</span></div>
        <div class="item"><span class="name">Lamb Bhuna Ghost</span><span class="price">$10.99</span><span class="desc">lamb with ginger and garlic</span></div>
        <div class="item"><span class="name">Lamb Vindaloo</span><span class="price">$10.99</span><span class="desc">lamb, potato, vinegar, chilli</span></div>
        <div class="item"><span class="name">Lamb Keema Mutter</span><span class="price">$12.99</span><span class="desc">minced lamb, onion, peas</span></div>
        <span class="dish dish--curry" role="img" aria-label="photo of a bowl of creamy curry"></span>
      </div>
    </div>
    <div class="heading"><span class="flourish" role="img" aria-label="gold scroll ornament"></span><span class="plate">Biryani &amp; Rice</span><span class="flourish" role="img" aria-label="gold scroll ornament"></span></div>
    <div class="cols">
      <div class="col">
        <div class="item"><span class="name">Chicken Biryani</span><span class="price">$7.99</span><span class="desc">chicken cooked with basmati rice</span></div>
        <div class="item"><span class="name">Goat Biryani</span><span class="price">$9.99</span><span class="desc">goat with long grain rice</span></div>
        <div class="item"><span class="name">Lamb Biryani</span><span class="price">$9.99</span><span class="desc">lamb on low heat with rice</span></div>
        <div class="item"><span class="name">Shrimp Biryani</span><span class="price">$10.99</span><span class="desc">shrimp with fragrant rice</span></div>
      </div>
      <div class="col">
        <div class="item"><span class="name">Vegetable Biryani</span><span class="price">$7.99</span><span class="desc">mixed vegetables and rice</span></div>
        <div class="item"><span class="name">Zeera Rice</span><span class="price">$3.99</span></div>
        <div class="item"><span class="name">Peas Pulao</span><span class="price">$5.99</span></div>
        <div class="item"><span class="name">Crown Spl. Biryani</span><span class="price">$11.99</span><span class="desc">chef's mix with saffron rice</span></div>
      </div>
    </div>
    <div class="spacer"></div>
    <span class="dish dish--biryani" role="img" aria-label="photo of a plate of biryani"></span>
  </div>
</section>

</body>
</html>
```